RiverPine - Rebranding, Namecard, Stationary and One Page Web

Refresh logo, make it modern and design matching name card, stationary and one page web

RiverPine Information Technology (Int'l) Company Limited
松河訊息科技(國際)有限公司

Company is System Integrator, and will be providing products and services to government and enterprise organizations. Our Chief Security Officer came from top U.S. vendor, and had been working on top enterprise and government projects globally, so we want the refreshed image of the new company to have a East Cost U.S. style, with hint of technology from Silicon Valley. The company will also be representing top brands from the U.S. on information security.

Branding refresh is needed because company is being acquired and is expanding

Target Market(s)

Cyber Security

Industry/Entity Type

Information Technology

Contact Information for Business Card

Need Chinese and English

Number of Pages Required

1 page

Font styles to use
Sans Serif

Colors
0292cd
00a990

Requirements
Must have
• Modern, clean, cyber look. Must keep same colors and general look and feel of original logo. Only modernization, do not change its personality

```html
<!DOCTYPE html>
<html lang="en">
<head>
<meta charset="utf-8">
<title>RiverPine Name Card</title>
<link rel="stylesheet" href="https://fonts.googleapis.com/css2?family=Open+Sans:ital,wght@0,400;0,600;0,700;1,800&family=Noto+Sans+TC:wght@400&display=swap">
<style>
  :root {
    --page-bg: #1b1b1c;
    --card-bg: #262627;
    --brand-blue: #0292cd;
    --brand-green: #00a990;
    --text-light: #e6e6e6;
    --text-white: #ffffff;
    --divider: #8a8a8a;
  }
  * { margin: 0; padding: 0; box-sizing: border-box; }
  html, body {
    width: 1200px; height: 1000px; overflow: hidden;
    background: var(--page-bg);
    font-family: "Open Sans", Arial, sans-serif;
  }
  .stage {
    position: relative; width: 1200px; height: 1000px;
  }
  .card {
    position: absolute; left: 260px; width: 680px; height: 390px;
    background: var(--card-bg);
    box-shadow: 0 10px 30px rgba(0,0,0,0.45);
  }
  .card--front { top: 75px; }
  .card--back { top: 525px; }

  /* Front */
  .brand-mark {
    position: absolute; top: 118px; left: 0; width: 100%;
    display: flex; justify-content: center; align-items: center; gap: 12px;
  }
  .brand-mark__dot {
    width: 20px; height: 20px; border-radius: 50%; background: var(--brand-green);
  }
  .brand-mark__name {
    font-size: 48px; font-weight: 700; color: var(--brand-blue); letter-spacing: 1px;
  }
  .company-name {
    position: absolute; top: 258px; left: 0; width: 100%; text-align: center;
  }
  .company-name__en {
    font-size: 15px; color: var(--brand-blue); letter-spacing: 0.3px;
  }
  .company-name__zh {
    font-family: "Noto Sans TC", "Open Sans", sans-serif;
    font-size: 15px; color: var(--brand-green); margin-top: 2px;
  }

  /* Back */
  .identity {
    position: absolute; top: 118px; right: 378px; text-align: right;
  }
  .identity__name {
    font-size: 28px; font-weight: 800; font-style: italic;
    color: var(--text-white); letter-spacing: 0.5px; line-height: 1.1;
  }
  .identity__title {
    font-size: 22px; font-weight: 600; color: var(--brand-blue); margin-top: 4px;
  }
  .divider {
    position: absolute; top: 120px; left: 318px; width: 2px; height: 66px;
    background: var(--divider);
  }
  .contacts {
    position: absolute; top: 118px; left: 336px; list-style: none;
  }
  .contacts__item {
    display: flex; align-items: center; gap: 14px;
    font-size: 17px; color: var(--text-light); height: 23px;
  }
  .contacts__icon { width: 13px; height: 13px; fill: var(--brand-blue); flex: none; }
  .contacts__accent { color: var(--brand-blue); }
  .address {
    position: absolute; top: 268px; left: 70px;
    display: flex; gap: 10px; font-size: 17px; color: var(--text-light); line-height: 1.35;
  }
  .address__brand { color: var(--brand-blue); font-weight: 700; white-space: nowrap; }
</style>
</head>
<body>
<main class="stage">
  <section class="card card--front" aria-label="Name card front">
    <div class="brand-mark">
      <span class="brand-mark__dot"></span>
      <span class="brand-mark__name">RiverPine</span>
    </div>
    <div class="company-name">
      <p class="company-name__en">RiverPine Information Technology (Int'l) Company Limited</p>
      <p class="company-name__zh">松河訊息科技(國際)有限公司</p>
    </div>
  </section>

  <section class="card card--back" aria-label="Name card back">
    <div class="identity">
      <p class="identity__name">DANIEL HO</p>
      <p class="identity__title">CEO</p>
    </div>
    <div class="divider"></div>
    <ul class="contacts">
      <li class="contacts__item">
        <svg class="contacts__icon" viewBox="0 0 24 24" aria-hidden="true"><path d="M6.6 10.8c1.4 2.8 3.8 5.1 6.6 6.6l2.2-2.2c.3-.3.7-.4 1-.2 1.1.4 2.3.6 3.6.6.6 0 1 .4 1 1V20c0 .6-.4 1-1 1C10.6 21 3 13.4 3 4c0-.6.4-1 1-1h3.5c.6 0 1 .4 1 1 0 1.3.2 2.5.6 3.6.1.3 0 .7-.2 1l-2.3 2.2z"/></svg>
        <span>(852) 5512 0946</span>
      </li>
      <li class="contacts__item">
        <svg class="contacts__icon" viewBox="0 0 24 24" aria-hidden="true"><path d="M2 5h20v14H2z M2 5l10 8 10-8" fill="none" stroke="#0292cd" stroke-width="2.5"/></svg>
        <span>danielho@hkriverpine.com.hk</span>
      </li>
      <li class="contacts__item">
        <svg class="contacts__icon" viewBox="0 0 24 24" aria-hidden="true"><circle cx="12" cy="12" r="10" fill="none" stroke="#0292cd" stroke-width="2"/><ellipse cx="12" cy="12" rx="4" ry="10" fill="none" stroke="#0292cd" stroke-width="2"/><path d="M2 12h20" stroke="#0292cd" stroke-width="2"/></svg>
        <span>www.<span class="contacts__accent">hkriverpine</span>.com.hk</span>
      </li>
    </ul>
    <div class="address">
      <span class="address__brand">RiverPine -</span>
      <p>Room B, Unit 402, 4/F, Lok Tin Ind. Bldg,<br>No. 15 Sheung Yee Road, Kowloon Bay, Kowloon, HKSAR</p>
    </div>
  </section>
</main>
</body>
</html>
```